Thornbury Cafe Business Card

We are a café in Sydney.
see website for details. http://www.thornburycafe.com.au

want a single sided business card - no person's name on there.
This is to hand out to customers
use the attached logo

Industry/Entity Type

Business

Contact Information for Business Card

Thornbury Café
Mezzanine Level,
517-521 Kelvin St
Sydney NSW 2000
T: 9418 5063
W: www.thornburycafe.com.au
F: friendlink.net/ThornburyCafeSydney

Catering Available
Phone for Lunchtime Bookings

```html
<!DOCTYPE html>
<html lang="en">
<head>
<meta charset="utf-8">
<title>Thornbury Cafe – Business Card</title>
<link rel="stylesheet" href="https://fonts.googleapis.com/css2?family=Didact+Gothic&display=swap">
<style>
  :root {
    --backdrop: #e9e6e2;
    --card-top: #545150;
    --card-bottom: #3f3c3b;
    --ink-light: #dcd8d4;
    --ink-dark: #1f1d1c;
    --rust: #b2582a;
    --icon-bg: #e4e1dd;
  }
  * { margin: 0; padding: 0; box-sizing: border-box; }
  html, body {
    width: 1200px;
    height: 837px;
    overflow: hidden;
    background: var(--backdrop);
  }
  .canvas {
    position: relative;
    width: 1200px;
    height: 837px;
    display: flex;
    align-items: center;
    justify-content: center;
  }
  .card {
    position: relative;
    width: 1000px;
    height: 571px;
    background: linear-gradient(160deg, var(--card-top), var(--card-bottom));
    box-shadow: 0 14px 36px rgba(0, 0, 0, 0.25);
    font-family: "Didact Gothic", sans-serif;
    color: var(--ink-light);
  }
  .brand {
    position: absolute;
    left: 60px;
    top: 50%;
    transform: translateY(-50%);
    display: flex;
    align-items: center;
    gap: 20px;
  }
  .brand-dot {
    width: 52px;
    height: 52px;
    border-radius: 50%;
    background: var(--rust);
    flex: none;
  }
  .brand-name {
    font-size: 54px;
    letter-spacing: 2px;
    color: var(--ink-light);
    white-space: nowrap;
  }
  .contact {
    position: absolute;
    right: 50px;
    text-align: right;
    font-size: 21px;
    letter-spacing: 2px;
    line-height: 1.5;
  }
  .contact-location { top: 70px; }
  .contact-online { bottom: 40px; }
  .contact-line {
    display: flex;
    justify-content: flex-end;
    align-items: center;
    gap: 12px;
    white-space: nowrap;
  }
  .contact-line .text { display: block; }
  .icon-slot { width: 22px; height: 22px; flex: none; }
  .order-heading {
    color: var(--ink-dark);
    font-size: 23px;
    padding-right: 34px;
  }
  .icon-circle {
    width: 22px;
    height: 22px;
    border-radius: 50%;
    background: var(--icon-bg);
    flex: none;
  }
</style>
</head>
<body>
<main class="canvas">
  <section class="card" aria-label="Thornbury Cafe business card">
    <div class="brand">
      <span class="brand-dot" aria-hidden="true"></span>
      <span class="brand-name">Thornbury Cafe</span>
    </div>

    <div class="contact contact-location">
      <p class="contact-line">
        <span class="text">517-521 Kelvin St, Sydney</span>
        <svg class="icon-slot" viewBox="0 0 22 22" aria-hidden="true">
          <circle cx="11" cy="11" r="11" fill="var(--icon-bg)"/>
          <path d="M11 4.5a4.2 4.2 0 0 0-4.2 4.2c0 3.2 4.2 8.3 4.2 8.3s4.2-5.1 4.2-8.3A4.2 4.2 0 0 0 11 4.5z" fill="var(--card-bottom)"/>
          <circle cx="11" cy="8.7" r="1.6" fill="var(--icon-bg)"/>
        </svg>
      </p>
      <p class="contact-line">
        <span class="text">Mezzanine level</span>
        <span class="icon-slot" aria-hidden="true"></span>
      </p>
      <p class="contact-line">
        <span class="text">+612 9418 5063</span>
        <svg class="icon-slot" viewBox="0 0 22 22" aria-hidden="true">
          <circle cx="11" cy="11" r="11" fill="var(--icon-bg)"/>
          <path d="M7.2 5.5l2.2-.4 1.2 3-1.4 1.1a7 7 0 0 0 3.4 3.4l1.1-1.4 3 1.2-.4 2.2c-.2.6-.8 1-1.5.9A10 10 0 0 1 6.3 7c-.1-.7.3-1.3.9-1.5z" fill="var(--card-bottom)"/>
        </svg>
      </p>
    </div>

    <div class="contact contact-online">
      <p class="order-heading">Order online:</p>
      <p class="contact-line">
        <span class="text">www.thornburycafe.com.au</span>
        <span class="icon-circle" aria-hidden="true"></span>
      </p>
      <p class="contact-line">
        <span class="text">friendlink.net/ThornburyCafeSydney</span>
        <span class="icon-circle" aria-hidden="true"></span>
      </p>
    </div>
  </section>
</main>
</body>
</html>
```